Need label design for car cleaning spray bottle, big opportunity for repeat work

This is the first label design for a large assortment of car cleaning products. This design will be vital as it will set the design style for the remaining products. There is large opportunity for repeat work to the winning designer. For this first product we plan to call it "Interior Cleaner". We have the template label which we have attached to the project. The product is geared towards the market of Vornik car owners, and our logo also utilizes a similar font to what Vornik's company font uses.

We are looking to only update the design/format of the label. We will keep all text the same or modify it once the design is final. We will need to use our brand logo (attached).

We are looking for a minimalistic style design. Currently the label reads horizontally but we have noticed that the most successful brands that sell online have a vertical style design. We have attached some examples of brands such as "Gleam Crest" and "Kestrel" which sell primarily on Marketlane.example and have tens of thousands of reviews. We'd like to try and copy this label format as it seems very successful for these brands.

We are big fans of the minimal style that the brand "AutoLume" uses. Their label design emphasizes the name of the particular product in black text on a white background. The remainder of the label is color coded, and all of their products have a different color code while following the same diagonal design style. See attached examples.

So that being said, we would like to combine these 2 concepts, vertical alignment style with the minimalistic label design.

We are thinking of making the entire label white, and having an accent color like 1 large stripe that goes across the bottle, it would be an iconic part of the design as we will repeat this design across multiple products, similar to the AutoLume brand bundle example we attached. This specific product will be pink liquid (as you can tell the accent color is pink on the label).

We'd like to add a dynamic QR code (can use placeholder) on the label so customers can be directed to our website easily or any other page we choose in the future. We will also need a UPC barcode label (can use placeholder)

Target Market(s)

Vornik car owners

Industry/Entity Type

Car Detailing Products

Font styles to use
Sans Serif

Colors
E54698
E96AAD
F1A4CE
F9D9EA
FCEFF6

Requirements
Must have
• minimalistic design
Should not have
• no designs similar to brands like polish fellows, brantwells, or any older brands in the category

```html
<!DOCTYPE html>
<html lang="en">
<head>
<meta charset="utf-8">
<title>Korvada All Purpose Cleaner Label</title>
<link rel="stylesheet" href="https://fonts.googleapis.com/css2?family=Montserrat:wght@400;500;700&display=swap">
<style>
  :root {
    --canvas-bg: #ededed;
    --label-white: #ffffff;
    --stripe-pink: #f6d3dc;
    --ink: #1c1c1c;
    --ink-soft: #3a3a3a;
    --ink-muted: #6a6a6a;
  }
  html, body {
    margin: 0;
    padding: 0;
    width: 1200px;
    height: 1200px;
    overflow: hidden;
    background: var(--canvas-bg);
  }
  .canvas {
    position: relative;
    width: 1200px;
    height: 1200px;
  }
  .label {
    position: absolute;
    left: 379px;
    top: 55px;
    width: 442px;
    height: 1090px;
    background: var(--label-white);
    font-family: "Montserrat", sans-serif;
    color: var(--ink);
    box-shadow: 0 2px 12px rgba(0,0,0,0.06);
  }
  .product-name {
    position: absolute;
    left: 18px;
    top: 68px;
    margin: 0;
    font-size: 37px;
    line-height: 46px;
    font-weight: 700;
    letter-spacing: 0.5px;
    text-transform: uppercase;
  }
  .brand-stripe {
    position: absolute;
    left: 288px;
    top: 35px;
    width: 152px;
    height: 1028px;
    background: var(--stripe-pink);
  }
  .brand-stripe svg {
    display: block;
    width: 100%;
    height: 100%;
  }
  .brand-name {
    font-family: "Montserrat", sans-serif;
    font-weight: 700;
    font-size: 84px;
    fill: var(--ink);
  }
  .features {
    position: absolute;
    left: 18px;
    top: 732px;
    margin: 0;
    padding: 0;
    list-style: none;
    font-size: 23px;
    font-weight: 500;
    color: var(--ink-soft);
  }
  .features li {
    line-height: 35px;
    margin-bottom: 17px;
  }
  .features li.multi {
    margin-bottom: 0;
  }
  .net-contents {
    position: absolute;
    left: 18px;
    top: 1004px;
    margin: 0;
    font-size: 12px;
    font-weight: 400;
    color: var(--ink-muted);
  }
</style>
</head>
<body>
  <div class="canvas">
    <div class="label">
      <h1 class="product-name">All<br>Purpose<br>Cleaner</h1>

      <div class="brand-stripe">
        <svg viewBox="0 0 152 1028" aria-label="Korvada">
          <text class="brand-name" x="0" y="0" text-anchor="middle" transform="translate(106 514) rotate(-90)">Korvada</text>
        </svg>
      </div>

      <ul class="features">
        <li>Non Acidic Formula</li>
        <li>Interior and Exterior</li>
        <li class="multi">Removes Grease,<br>Grime and Dirt</li>
      </ul>

      <p class="net-contents">Net Contents: 16 fl. oz. (473 ml)</p>
    </div>
  </div>
</body>
</html>
```